Fine Art business needs new website

We need a simple website with a home page, about us page, New sculptures, Sold sculptures, and a contact us page.Our sculptures are very high end one of a kind pieces. As such we need the site to be VERY elegant and professional. Lastly, because I'll be updating pictures on the website on a monthly basis it needs to be user friendly to update (Wordpress is preferred). The only branding we have so far for the business is a business card.
Updates
I wasn't completely ready when this project launched, also I am on the road right now and haven't been able to be as responsive to all you designers as I would like. I will work on giving feedback to all the top designs we've received so far. Thank you all so much for your participation and hardwork.
Target Market(s)
High end customers (affluent), art collectors, interior decorators/designers
Industry/Entity Type
Art Gallery
Coding
Coded - Design and coding required
Number of Pages Required
5+ page
Requirements
Must have
- Easily editable picture gallery for myself so that I can add new pieces(pictures of the pieces), remove sold pieces, etc. I would like the website to be built in wordpress so I can update it. I currently use mangewordpress through Netmarro for my other business website and would like to do the same for this one.
- Pages:
- -Intro page with featured pieces
- -Current pieces gallery (for sale) mainly a picture gallery
- -Sculptures archive (sold pieces) another picture gallery
- -About us: Pull-down of -about the artist (attached content)
- -Artistic Process (attached content)
- -Show Schedule:
- -one page dedicated to "friends of TMV" (basically a link page)
- TO BE CLEAR "www.pineroverslane.com" IS A TOTALLY DIFFERENT SITE AND I'M NOT TRYING TO COMBINE THE TWO OR JOIN THEM INTO ONE. This page needs be more elegant and seperate from the Pine Rovers site.
- UPDATE: I'd like a link to the TMV Faceplume page: https://www.faceplume-social.com/mirelcraftworks/
Nice to have
- I would like the pictures on the gallery pages able to have text connected with them (Materials, price)
- I would like the site style and fonts to be similar to our business cards we've already had designed (picture attached).
Should not have
- Too much flash or other things that will make the site slow to load.

```html
<!DOCTYPE html>
<html lang="en">
<head>
<meta charset="utf-8">
<title>Sold Sculptures – Terra Mira Vault</title>
<link href="https://fonts.googleapis.com/css2?family=Cinzel:wght@400;700&family=Cormorant+Garamond:wght@500&family=Poppins:wght@300;400;500&family=Raleway:wght@400&display=swap" rel="stylesheet">
<style>
:root{
  --ink:#1e1e1e;
  --muted:#555;
  --line:#cfcfcf;
  --purple:#5c0f8e;
  --deep-purple:#3e1a4a;
  --sold-red:#e3081d;
  --white:#ffffff;
  --fb:#5d2fa6;
  --ig:#7b1f4a;
  --gp:#b3261e;
  --mail:#1f5e9c;
}
*{margin:0;padding:0;box-sizing:border-box}
html,body{width:1200px;height:2187px;overflow:hidden;background:var(--white)}
body{position:relative;font-family:"Poppins",sans-serif;color:var(--ink)}
.abs{position:absolute}

/* top bar */
.contact-line{left:99px;display:flex;align-items:center;gap:12px;font-size:13px;font-weight:300;color:var(--muted)}
.contact-line .icon{width:27px;height:27px;border:1px solid #999;border-radius:50%;display:flex;align-items:center;justify-content:center}
.brand{left:0;width:1200px;text-align:center;font-family:"Cinzel",serif;color:var(--ink)}
.brand-top{top:115px;font-size:19px;letter-spacing:3px}
.socials{display:flex;gap:17px}
.socials-top{left:901px;top:4px}
.social{width:37px;height:37px;border-radius:50%;display:flex;align-items:center;justify-content:center;color:var(--white);font-family:"Poppins",sans-serif;font-size:11px;font-weight:500}
.social.fb{background:var(--fb)}.social.ig{background:var(--ig)}.social.gp{background:var(--gp)}.social.mail{background:var(--mail)}

/* nav */
.main-nav{left:0;top:187px;width:1200px;height:49px;border-top:1px solid var(--line);border-bottom:1px solid var(--line)}
.main-nav a{position:absolute;top:14px;transform:translateX(-50%);font-family:"Cormorant Garamond",serif;font-weight:500;font-size:15px;color:var(--ink);text-decoration:none;white-space:nowrap}
.main-nav .search{top:16px}

/* hero */
.hero{left:0;top:236px;width:1200px;height:332px;background:radial-gradient(ellipse at 30% 40%,#6b3f9c 0%,#3a1a5e 45%,#1c0c2e 100%)}
.hero-title{left:0;top:358px;width:1200px;text-align:center;font-family:"Cinzel",serif;font-weight:700;font-size:70px;color:var(--white)}

/* gallery */
.section-title{left:0;top:655px;width:1200px;text-align:center;font-family:"Cinzel",serif;font-size:46px;font-weight:400}
.card{width:321px;height:349px;background:var(--white);box-shadow:0 4px 14px rgba(0,0,0,.12)}
.card .photo{height:285px}
.card .badge{position:absolute;left:12px;top:13px;width:77px;height:24px;border-radius:12px;background:var(--sold-red);color:var(--white);font-size:11px;display:flex;align-items:center;justify-content:center}
.card .name{position:absolute;left:24px;top:303px;font-size:19px;font-weight:500}
.card .price{position:absolute;right:24px;top:307px;font-size:15px;font-weight:400}
.btn-view{left:523px;top:1556px;width:154px;height:48px;background:var(--purple);color:var(--white);font-size:17px;font-weight:500;display:flex;align-items:center;justify-content:center}

/* footer */
.brand-foot{top:1770px;font-size:14px;letter-spacing:2px}
.touch{left:0;top:1826px;width:1200px;text-align:center;font-family:"Cinzel",serif;font-size:27px}
.touch-copy{left:360px;top:1874px;width:480px;text-align:center;font-family:"Raleway",sans-serif;font-size:15px;line-height:25px}
.subscribe{left:372px;top:1955px;width:458px;height:45px;display:flex}
.subscribe .field{flex:1;border:1px solid #aaa;border-right:none;padding-left:14px;display:flex;align-items:center;font-size:14px;color:var(--muted)}
.subscribe .go{width:129px;background:var(--deep-purple);color:var(--white);display:flex;align-items:center;justify-content:center;font-size:15px;letter-spacing:1.5px}
.socials-foot{left:501px;top:2027px}
.copyright{left:0;top:2147px;width:1200px;text-align:center;font-size:12px;font-weight:300;color:var(--muted)}
</style>
</head>
<body>

<header>
  <div class="abs contact-line" style="top:10px">
    <span class="icon"><svg width="13" height="13" viewBox="0 0 24 24"><path fill="#777" d="M6.6 10.8a15 15 0 006.6 6.6l2.2-2.2a1 1 0 011-.25 11.4 11.4 0 003.6.57 1 1 0 011 1V20a1 1 0 01-1 1A17 17 0 013 4a1 1 0 011-1h3.5a1 1 0 011 1c0 1.25.2 2.45.57 3.57a1 1 0 01-.25 1z"/></svg></span>
    (555) 014-2290
  </div>
  <div class="abs contact-line" style="top:48px">
    <span class="icon"><svg width="13" height="11" viewBox="0 0 24 18"><rect width="24" height="18" rx="2" fill="#777"/><path d="M1 2l11 8 11-8" stroke="#fff" stroke-width="2" fill="none"/></svg></span>
    ivo@pineroverslane.com
  </div>

  <div class="abs brand brand-top">TERRA MIRA VAULT</div>

  <div class="abs socials socials-top">
    <span class="social fb">FP</span>
    <span class="social ig">LN</span>
    <span class="social gp">OR</span>
    <span class="social mail"><svg width="16" height="12" viewBox="0 0 24 18"><rect width="24" height="18" rx="2" fill="#fff"/><path d="M1 2l11 8 11-8" stroke="#1f5e9c" stroke-width="2" fill="none"/></svg></span>
  </div>

  <nav class="abs main-nav">
    <a style="left:234px">HOME</a>
    <a style="left:354px">ABOUT US</a>
    <a style="left:511px">NEW SCULPTURES</a>
    <a style="left:694px">SOLD SCULPTURES</a>
    <a style="left:862px">CONTACT US</a>
    <a class="search" style="left:978px"><svg width="12" height="12" viewBox="0 0 24 24"><circle cx="10" cy="10" r="7" stroke="#1e1e1e" stroke-width="3" fill="none"/><path d="M15 15l7 7" stroke="#1e1e1e" stroke-width="3"/></svg></a>
  </nav>
</header>

<div class="abs hero" role="img" aria-label="Close-up photograph of dark purple amethyst crystals"></div>
<h1 class="abs hero-title">SOLD SCULPTURES</h1>

<main>
  <h2 class="abs section-title">SOLD SCULPTURES</h2>

  <article class="abs card" style="left:99px;top:752px">
    <div class="photo" role="img" aria-label="Orange crystal-lined geode on a black stand" style="background:radial-gradient(circle at 50% 45%,#b8652a 0%,#5a2e12 35%,#111 70%)"></div>
    <span class="badge">SOLD OUT</span><span class="name">SCULPTURE-1</span><span class="price">$12.00</span>
  </article>
  <article class="abs card" style="left:439px;top:752px">
    <div class="photo" role="img" aria-label="Small polished geodes arranged below a cloth pouch" style="background:linear-gradient(180deg,#d9d3c4 0%,#3a3632 50%,#1a1a1a 100%)"></div>
    <span class="badge">SOLD OUT</span><span class="name">SCULPTURE-1</span><span class="price">$12.00</span>
  </article>
  <article class="abs card" style="left:779px;top:752px">
    <div class="photo" role="img" aria-label="Clear quartz crystal cavity glowing blue" style="background:linear-gradient(135deg,#3a4f6a 0%,#9fb8d6 50%,#2b3345 85%,#e06a1a 100%)"></div>
    <span class="badge">SOLD OUT</span><span class="name">SCULPTURE-1</span><span class="price">$12.00</span>
  </article>

  <article class="abs card" style="left:99px;top:1146px">
    <div class="photo" role="img" aria-label="Open geode with purple amethyst centre and golden bands" style="background:radial-gradient(ellipse at 45% 45%,#8a6f86 0%,#6a5a6e 35%,#b89a4a 60%,#d9cbb8 85%)"></div>
    <span class="badge">SOLD OUT</span><span class="name">SCULPTURE-1</span><span class="price">$12.00</span>
  </article>
  <article class="abs card" style="left:439px;top:1146px">
    <div class="photo" role="img" aria-label="Iridescent titanium-coated quartz cluster on black" style="background:radial-gradient(circle at 50% 55%,#9a8aa8 0%,#4a3d52 30%,#0a0a0a 65%)"></div>
    <span class="badge">SOLD OUT</span><span class="name">SCULPTURE-1</span><span class="price">$12.00</span>
  </article>
  <article class="abs card" style="left:779px;top:1146px">
    <div class="photo" role="img" aria-label="Two halves of a banded agate geode held in hand" style="background:linear-gradient(160deg,#6b4a3a 0%,#2a2a30 40%,#8a8f9a 60%,#b07a4a 100%)"></div>
    <span class="badge">SOLD OUT</span><span class="name">SCULPTURE-1</span><span class="price">$12.00</span>
  </article>

  <a class="abs btn-view">VIEW ALL</a>
</main>

<footer>
  <div class="abs brand brand-foot">TERRA MIRA VAULT</div>
  <h3 class="abs touch">Get In Touch With Us</h3>
  <p class="abs touch-copy">At vero eos et accusamus et iusto odio dignissimos ducimus qui blanditiis praesentium voluptatum deleniti atque</p>
  <form class="abs subscribe">
    <span class="field">Enter Your Email Addresss</span>
    <span class="go">SUBSCRIBE</span>
  </form>
  <div class="abs socials socials-foot">
    <span class="social fb">FP</span>
    <span class="social ig">LN</span>
    <span class="social gp">OR</span>
    <span class="social mail"><svg width="16" height="12" viewBox="0 0 24 18"><rect width="24" height="18" rx="2" fill="#fff"/><path d="M1 2l11 8 11-8" stroke="#1f5e9c" stroke-width="2" fill="none"/></svg></span>
  </div>
  <p class="abs copyright">© Copyrights.2018.Terra Mira Vault.All Rights Reserved</p>
</footer>

</body>
</html>
```